Cat-products company needs smart, yet endearing, business card

We need a business card design for a new, but up-and-running, business based in Honolulu, Hawaii. The business is Purrnest Nook Co. Our first product is the most environmentally-friendly cat grass kit ever seen on the planet. Future products, currently in the R&D phase, will include a variety of exciting cat scratchers. We also do consulting work to help apartment-dwellers make their home more cat-friendly and, in the future, plan on doing full, custom installs of structure to create high walkways for cats.

Target Market(s)

Middle-aged, apartment-dwelling, middle-class workers who own 1 or more cats and who dote on them.

Industry/Entity Type

Pet Care

Contact Information for Business Card

A striking, professional, yet warm and friendly design is what we're after.

Font styles to use
Serif
Sans Serif
Other font styles liked:
• Comfortaa

Colors

Designer to choose colors to be used in the design.

Requirements
Must have
• The company logo: (see attachment)
• The company name: Purrnest Nook Co
• The web address: www.purrnestnookco.com
• Email: support@purrnestnookco.com
• Phone: +1 (808) 571 6023
• Update (Fri Jun 30 3017 7:45pm Hawaii Time) I would like, is possible, uploaded picture of the cat grass kit on the back of the card with some text along the lines of: Purrnest Nook Co - Maker Of The Leafiest Feline Sprout Set Yet
Nice to have
• A cat picture, cartoon, real or silhouette that illustrates cats in action and/or relaxing; ie using the apartment space to live, play and relax in and being well-contented.
• Most of the website is done in the font: Comfortaa. It might be nice to continue using this for brand consistency.
Should not have
• Hard-to-read fonts.

```html
<!DOCTYPE html>
<html lang="en">
<head>
<meta charset="utf-8">
<title>Purrnest Nook Co – Business Card</title>
<link href="https://fonts.googleapis.com/css2?family=Comfortaa:wght@400;700&display=swap" rel="stylesheet">
<style>
  :root {
    --backdrop: #86710c;
    --card-green: #5e9a4c;
    --brand-brown: #5b3a2e;
    --brand-yellow: #f5ae1c;
    --accent-green: #5cb947;
    --icon-red: #8a1c12;
    --white: #ffffff;
  }
  * { box-sizing: border-box; margin: 0; padding: 0; }
  html, body { width: 1200px; height: 1200px; overflow: hidden; }
  body {
    background: var(--backdrop);
    font-family: "Comfortaa", sans-serif;
    position: relative;
  }

  /* Front of card */
  .card-front {
    position: absolute; left: 54px; top: 105px;
    width: 840px; height: 480px;
    background: var(--card-green);
  }
  .brand-name {
    position: absolute; left: 60px; top: 170px; width: 300px;
    text-align: center;
    font-weight: 700; font-size: 44px; line-height: 1.1;
    color: var(--brand-yellow);
  }
  .divider {
    position: absolute; left: 420px; top: 93px;
    width: 2px; height: 264px;
    background: #a9762f;
  }
  .person-name {
    position: absolute; left: 479px; top: 90px;
    font-size: 20px; font-weight: 400;
    color: var(--brand-brown);
  }
  .person-name .surname { color: var(--brand-yellow); }
  .person-role {
    position: absolute; left: 479px; top: 120px;
    font-size: 11px; color: #7d8f3c;
  }
  .contact-list { list-style: none; }
  .contact-item {
    position: absolute; left: 480px;
    display: flex; align-items: center;
    font-size: 13px; color: var(--brand-yellow);
  }
  .contact-item svg { width: 16px; height: 16px; margin-right: 42px; }
  .contact-phone { top: 194px; }
  .contact-email { top: 253px; }
  .contact-web   { top: 306px; }
  .mascot-illustration {
    position: absolute; left: 724px; top: 389px;
    width: 72px; height: 62px;
    background: linear-gradient(135deg, #a87b3c, #6b4a2a);
    border-radius: 8px;
  }

  /* Back of card */
  .card-back {
    position: absolute; left: 273px; top: 644px;
    width: 840px; height: 480px;
    overflow: hidden;
  }
  .back-photo {
    position: absolute; inset: 0;
    background:
      radial-gradient(ellipse at 50% 45%, #8a8f7c 0%, #6b6f5c 40%, transparent 70%),
      linear-gradient(180deg, #5d6a4e 0%, #4f6e3e 60%, #3f7a36 100%);
  }
  .back-frame {
    position: absolute; left: 11px; top: 11px; right: 11px; bottom: 11px;
    border: 2px solid var(--accent-green);
  }
  .back-title {
    position: absolute; left: 0; right: 0; top: 142px;
    text-align: center;
    font-size: 21px; color: var(--accent-green);
  }
  .back-tagline {
    position: absolute; left: 50%; top: 348px;
    transform: translateX(-50%);
    white-space: nowrap;
    background: var(--accent-green);
    color: var(--white);
    font-size: 20px;
    padding: 18px 12px;
  }
</style>
</head>
<body>

<section class="card-front">
  <div class="brand-name">Purrnest<br>Nook Co</div>
  <div class="divider"></div>
  <h1 class="person-name">Marcus <span class="surname">Kealoha</span></h1>
  <p class="person-role">CEO</p>
  <ul class="contact-list">
    <li class="contact-item contact-phone">
      <svg viewBox="0 0 16 16"><path fill="var(--icon-red)" d="M3.5 1.5l2.5 0 1 3.5-1.6 1.2c.8 1.8 2.2 3.2 4 4l1.2-1.6 3.5 1v2.5c0 .8-.7 1.4-1.5 1.4C7 13.3 2.7 9 2.1 3c0-.8.6-1.5 1.4-1.5z"/></svg>
      +1 (808) 571 6023
    </li>
    <li class="contact-item contact-email">
      <svg viewBox="0 0 16 16"><rect x="1" y="3" width="14" height="10" fill="var(--icon-red)"/><path d="M1 3l7 6 7-6M1 13l5-5M15 13l-5-5" stroke="#e8b0a0" stroke-width="1" fill="none"/></svg>
      support@purrnestnookco.com
    </li>
    <li class="contact-item contact-web">
      <svg viewBox="0 0 16 16" fill="none" stroke="#8a5a2e" stroke-width="1"><circle cx="8" cy="8" r="6.5"/><ellipse cx="8" cy="8" rx="3" ry="6.5"/><path d="M1.5 8h13M2.5 4.8h11M2.5 11.2h11"/></svg>
      www.purrnestnookco.com
    </li>
  </ul>
  <div class="mascot-illustration" role="img" aria-label="Small illustration of a sitting tabby cat"></div>
</section>

<section class="card-back">
  <div class="back-photo" role="img" aria-label="Photo of a fluffy kitten peeking through green grass"></div>
  <div class="back-frame"></div>
  <h2 class="back-title">Purrnest Nook Co</h2>
  <p class="back-tagline">Maker Of The Leafiest Feline Sprout Set Yet</p>
</section>

</body>
</html>
```